Looking for a5 flyer for domestic properties in Scotland
One side on Air Source Heat pumps (air to water Heat pump) Instalation + maintenance
Other side Air to Air Heat Pumps also knows as Air Conditioning Heat Pumps. Installation
Design to be Black white with red blue
Harlow- Climawell Services

Need sell the benifts of large energy savings over oil and lpg and lowering carbon footprint

```html
<!DOCTYPE html>
<html lang="en">
<head>
<meta charset="utf-8">
<title>Harlow Climawell Services – Heat Pump Flyers</title>
<link rel="stylesheet" href="https://fonts.googleapis.com/css2?family=Anton&family=Montserrat:wght@400;500;600;700&family=Poppins:wght@600;700&display=swap">
<style>
:root{
  --orange:#E8491D;
  --blue:#29A3DC;
  --black:#111111;
  --white:#ffffff;
  --ink:#1d1d1d;
  --page:#e4e4e4;
}
*{box-sizing:border-box;margin:0;padding:0}
html,body{width:795px;height:1200px;overflow:hidden;background:var(--page)}
.sheet{position:relative;width:795px;height:1200px;overflow:hidden}
.flyer{position:absolute;left:192px;width:628px;height:890px;transform-origin:0 0;transform:scale(.655);background:var(--white);overflow:hidden;font-family:'Montserrat',sans-serif;color:var(--ink);box-shadow:0 4px 14px rgba(0,0,0,.25)}
.flyer--ashp{top:11px}
.flyer--ac{top:606px}
.art{position:absolute;left:0;top:0}
.abs{position:absolute}

/* shared type */
.col-head{font-family:'Poppins',sans-serif;font-weight:700;font-size:17px;letter-spacing:.2px;line-height:1.1}
.body-text{font-size:12px;line-height:1.2}
.headline{font-family:'Anton',sans-serif;font-size:30px;line-height:1.08;color:var(--black);letter-spacing:.2px}
.headline .accent{display:block;color:var(--orange)}

/* brand */
.brand{left:43px;top:40px}
.brand-name{font-family:'Anton',sans-serif;font-size:46px;line-height:1;color:var(--black)}
.brand-tag{font-family:'Montserrat',sans-serif;font-weight:700;font-size:12.5px;color:var(--black);margin-top:3px}

/* ASHP side */
.flyer--ashp .headline{left:43px;top:118px}
.ashp-intro{left:43px;top:192px;width:335px}
.benefits{left:43px;top:273px;list-style:none;color:var(--white);font-size:11.5px;line-height:14.4px}
.benefits li,.ac-points li{position:relative;padding-left:13px}
.benefits li::before,.ac-points li::before{content:"";position:absolute;left:0;top:4px;width:6px;height:6px;border-radius:50%;border:1.6px solid var(--blue)}
.grant{left:43px;top:390px;width:540px;height:25px;border:1.6px solid var(--white);border-radius:13px;display:flex;align-items:center;color:var(--white);font-family:'Poppins',sans-serif;font-weight:600;font-size:14.5px;white-space:nowrap}
.grant-label{background:var(--orange);border:1.6px solid var(--white);border-radius:13px;height:25px;margin-left:-1.6px;padding:0 11px;display:flex;align-items:center;margin-right:9px;letter-spacing:.3px}
.grant-amount{color:var(--blue);margin:0 4px}
.maintenance{left:43px;top:437px;width:255px}
.maintenance .col-head{color:var(--blue);margin-bottom:6px}
.maintenance ul{list-style:none}
.maintenance li{position:relative;padding-left:20px;margin-bottom:12px}
.maintenance li::before{content:"";position:absolute;left:1px;top:4px;width:7px;height:7px;border-radius:50%;border:1.8px solid var(--orange)}
.ashp-install{left:330px;top:437px;width:252px;color:var(--white)}
.ashp-install p{margin-top:5px}

/* AC side */
.flyer--ac .headline{left:43px;top:42px}
.ac-intro{left:43px;top:114px;width:258px}
.ac-points{list-style:none;font-size:11.5px;line-height:14.4px}
.ac-points--a{left:43px;top:208px}
.ac-points--b{left:221px;top:208px}
.steps{left:43px;top:300px;width:258px}
.steps .col-head{color:var(--blue);margin-bottom:10px}
.step{margin-bottom:13px}
.step-tag{display:flex;align-items:center;height:14px;margin-bottom:5px}
.step-num{width:14px;height:14px;background:var(--black);color:var(--white);font-family:'Poppins',sans-serif;font-weight:700;font-size:10px;display:flex;align-items:center;justify-content:center;margin-right:4px}
.step-label{height:14px;background:var(--orange);color:var(--white);font-family:'Poppins',sans-serif;font-weight:600;font-size:10.5px;padding:0 14px 0 5px;display:flex;align-items:center;clip-path:polygon(0 0,100% 0,calc(100% - 6px) 100%,0 100%);position:relative}
.step-slash{width:3px;height:14px;background:var(--blue);transform:skewX(-25deg);margin-left:1px}
.commercial{left:331px;top:297px;width:270px;color:var(--white)}
.commercial-title{font-family:'Poppins',sans-serif;font-weight:700;font-size:19px;line-height:1.1}
.commercial-sub{font-family:'Poppins',sans-serif;font-weight:700;font-size:14px;margin:3px 0 0 2px}
.commercial .col-head{color:var(--blue);margin-top:6px}
.feature{position:absolute;left:331px;width:270px;display:flex;gap:9px;color:var(--white)}
.feature-icon{flex:0 0 34px;width:34px;height:34px;background:var(--blue);display:flex;align-items:center;justify-content:center;margin-top:2px}
.feature p{width:212px}
.feature--1{top:392px}
.feature--2{top:490px}
.feature--3{top:582px}

/* footer */
.cta{left:135px;top:790px;width:364px;height:26px;display:flex;align-items:center;justify-content:center;font-family:'Poppins',sans-serif;font-weight:700;font-size:15px;color:var(--white);letter-spacing:.2px}
.footer-contacts{left:0;top:830px;width:628px;display:flex;justify-content:space-between;padding:0 44px;color:var(--white);font-family:'Poppins',sans-serif;font-weight:600;font-size:13.5px}
.contact{display:flex;align-items:center;gap:5px;white-space:nowrap}
</style>
</head>
<body>
<main class="sheet">

  <!-- Side 1: air source heat pumps -->
  <article class="flyer flyer--ashp">
    <svg class="art" width="628" height="890" viewBox="0 0 628 890">
      <defs>
        <linearGradient id="ashpWall" x1="0" y1="0" x2="1" y2="1">
          <stop offset="0" stop-color="#c9a47a"/>
          <stop offset=".5" stop-color="#e8e6e2"/>
          <stop offset="1" stop-color="#6f8f4a"/>
        </linearGradient>
        <linearGradient id="ashpProduct" x1="0" y1="0" x2="0" y2="1">
          <stop offset="0" stop-color="#f4f4f4"/>
          <stop offset="1" stop-color="#a3a3a3"/>
        </linearGradient>
      </defs>
      <rect x="0" y="260" width="628" height="169" fill="var(--black)"/>
      <rect x="313" y="429" width="315" height="370" fill="var(--orange)"/>
      <polygon points="440,0 458,0 372,132 355,132" fill="var(--black)"/>
      <polyline points="463,0 376,133 454,292 628,292" fill="none" stroke="var(--orange)" stroke-width="3"/>
      <polygon role="img" aria-label="Photo of an outdoor air source heat pump unit on a timber-clad wall above shrubs" points="472,0 628,0 628,286 459,286 383,132" fill="url(#ashpWall)"/>
      <rect role="img" aria-label="Product photo of air to water heat pump units and an indoor cylinder" x="327" y="602" width="262" height="160" rx="3" fill="url(#ashpProduct)"/>
      <rect x="0" y="799" width="628" height="91" fill="var(--black)"/>
      <rect x="0" y="799" width="628" height="3" fill="var(--blue)"/>
      <polygon points="128,790 506,790 494,816 140,816" fill="var(--blue)"/>
    </svg>

    <div class="abs brand">
      <div class="brand-name">Harlow</div>
      <div class="brand-tag">Climawell Services</div>
    </div>

    <h1 class="abs headline"><span class="accent">AIR SOURCE HEAT</span>PUMPS FOR THE HOME</h1>
    <p class="abs body-text ashp-intro">Air Source Heat Pumps (ASHP) are the new green alternative to your oil or gas boiler for your homes heating and hot water requirements that will help build towards a cleaner environment for future generations</p>

    <ul class="abs benefits">
      <li>Reduce your energy bills</li>
      <li>Safeguard against rising fuel prices.</li>
      <li>No chimneys or flues producing harmful emissions</li>
      <li>Raise your property value</li>
      <li>Reduce your home's carbon footprint</li>
      <li>Power your home with 100% renewable energy</li>
      <li>Receive as much as £13,900 in payment from the Renewable Heat Incentive</li>
    </ul>

    <div class="abs grant"><span class="grant-label">Tax-FREE Income</span>up to<span class="grant-amount">£13,900</span>Grant from the Government</div>

    <section class="abs maintenance">
      <h2 class="col-head">MAINTENANCE</h2>
      <ul class="body-text">
        <li>To optimise performance, increase energy efficiency, improve air quality and increase reliability of your air conditioning system, we recommend carrying out preventative planned maintenance of your equipment.</li>
        <li>During our maintenance visit, we clean and sanitise indoor coils, pumps and drains to kill any bacteria, acid foam clean the outdoor coil and perform various other performance tests that will help our engineers spot minor problems before they develop into serious ones.</li>
        <li>All these details are logged on our Servicelog system, which generates reports for our clients that comply with regulation. This high quality, hi-tec maintenance ensures that everything is running as it should.</li>
      </ul>
    </section>

    <section class="abs ashp-install">
      <h2 class="col-head">INSTALLATION</h2>
      <p class="body-text">Our experienced teams of installers at Harlow Climawell Services have had specialist training with manufacturers, such as Norvale. Our installations are all MCS accredited which allows access to the financial incentives. All of our air source heat pump installations are protected under warranty for your peace of mind.</p>
    </section>

    <div class="abs cta">CONTACT US FOR MORE INFORMATION</div>
    <div class="abs footer-contacts">
      <span class="contact"><svg width="13" height="13" viewBox="0 0 24 24"><path fill="var(--orange)" d="M6.6 10.8a15.1 15.1 0 0 0 6.6 6.6l2.2-2.2a1 1 0 0 1 1-.25 11.4 11.4 0 0 0 3.6.57 1 1 0 0 1 1 1V20a1 1 0 0 1-1 1A17 17 0 0 1 3 4a1 1 0 0 1 1-1h3.5a1 1 0 0 1 1 1c0 1.25.2 2.45.57 3.57a1 1 0 0 1-.25 1z"/></svg>0800 555 0142</span>
      <span class="contact"><svg width="15" height="11" viewBox="0 0 18 14"><rect width="18" height="14" rx="1" fill="var(--orange)"/><path d="M1 1l8 6 8-6" fill="none" stroke="var(--black)" stroke-width="1.5"/></svg>info@harlowclimawell.co</span>
      <span class="contact"><svg width="13" height="13" viewBox="0 0 16 16"><g fill="none" stroke="var(--orange)" stroke-width="1.4"><circle cx="8" cy="8" r="7"/><ellipse cx="8" cy="8" rx="3" ry="7"/><path d="M1 8h14M2.5 4.5h11M2.5 11.5h11"/></g></svg>www.harlowclimawell.co</span>
    </div>
  </article>

  <!-- Side 2: air to air heat pumps -->
  <article class="flyer flyer--ac">
    <svg class="art" width="628" height="890" viewBox="0 0 628 890">
      <defs>
        <linearGradient id="acRoom" x1="0" y1="0" x2="1" y2="0">
          <stop offset="0" stop-color="#ffffff"/>
          <stop offset=".55" stop-color="#f1f1f1"/>
          <stop offset="1" stop-color="#d6d6d6"/>
        </linearGradient>
        <linearGradient id="acUnit" x1="0" y1="0" x2="0" y2="1">
          <stop offset="0" stop-color="#fbfbfb"/>
          <stop offset="1" stop-color="#cfcfcf"/>
        </linearGradient>
      </defs>
      <rect role="img" aria-label="Photo of a white wall-mounted air conditioning unit in a bright room" x="0" y="0" width="628" height="270" fill="url(#acRoom)"/>
      <polygon points="0,270 420,270 410,282 0,282" fill="var(--black)"/>
      <polygon points="426,270 628,270 628,282 416,282" fill="var(--blue)"/>
      <rect x="316" y="282" width="312" height="517" fill="var(--orange)"/>
      <rect role="img" aria-label="Product photo of a white wall-mounted indoor air conditioning unit" x="346" y="684" width="222" height="81" rx="3" fill="url(#acUnit)"/>
      <rect x="0" y="799" width="628" height="91" fill="var(--black)"/>
      <rect x="0" y="799" width="628" height="3" fill="var(--blue)"/>
      <polygon points="128,790 506,790 494,816 140,816" fill="var(--blue)"/>
    </svg>

    <h1 class="abs headline"><span class="accent">AIR CONDITIONING</span>FOR THE HOME</h1>
    <p class="abs body-text ac-intro">Enhance the comfort of your home with an Air Conditioning heat pump. We supply and fit latest energy-efficient systems to keep your living space at the right temperature all year round and help reduce your heating bills.</p>
    <ul class="abs ac-points ac-points--a">
      <li>Cools in summer</li>
      <li>Efficiently heats in winter</li>
      <li>Reduce heating bills</li>
    </ul>
    <ul class="abs ac-points ac-points--b">
      <li>Purifies the air</li>
      <li>Dehumidifier</li>
      <li>Energy efficient systems</li>
    </ul>

    <section class="abs steps">
      <h2 class="col-head">STEPS FOR INSTALLATION</h2>
      <div class="step">
        <div class="step-tag"><span class="step-num">1</span><span class="step-label">Get in Touch Today</span><span class="step-slash"></span></div>
        <p class="body-text">Book in a survey with our team today who will access your requirements to find the right solution</p>
      </div>
      <div class="step">
        <div class="step-tag"><span class="step-num">2</span><span class="step-label">Free Home Survey</span><span class="step-slash"></span></div>
        <p class="body-text">We would then visit your property and make recommendations of which air conditioning unit would suit your requirements We'll also run over the siting and installation process.</p>
      </div>
      <div class="step">
        <div class="step-tag"><span class="step-num">3</span><span class="step-label">Quotation</span><span class="step-slash"></span></div>
        <p class="body-text">We will select the correct air conditioning for your property's heat/cool requirements and email across a quotation.</p>
      </div>
      <div class="step">
        <div class="step-tag"><span class="step-num">4</span><span class="step-label">Installation</span><span class="step-slash"></span></div>
        <p class="body-text">Your installation will then be booked in with our experienced teams who have had specialist training with manufacturers, such as Norvale, Kestrel and Tornell. We take care of all aspects of installation for a hassle free experience. All of our air conditioning installations are protected under warranty for your peace of mind</p>
      </div>
    </section>

    <section class="abs commercial">
      <h2 class="commercial-title">COMMERCIAL AIR CONDITIONING</h2>
      <div class="commercial-sub">SOLUTION FOR BUSINESS</div>
      <h3 class="col-head">INSTALLATION</h3>
    </section>

    <div class="feature feature--1">
      <span class="feature-icon"><svg width="22" height="22" viewBox="0 0 24 24" fill="none" stroke="#fff" stroke-width="1.5"><circle cx="12" cy="7" r="3"/><circle cx="5" cy="10" r="2.3"/><circle cx="19" cy="10" r="2.3"/><path d="M7 20v-3a5 5 0 0 1 10 0v3M1.5 19v-2a3.5 3.5 0 0 1 5-3M22.5 19v-2a3.5 3.5 0 0 0-5-3"/></svg></span>
      <p class="body-text">We work alongside other specialists like architects, consultants, designers and shopfitters in the design stage and install the best possible solution for the end user.</p>
    </div>
    <div class="feature feature--2">
      <span class="feature-icon"><svg width="22" height="22" viewBox="0 0 24 24" fill="none" stroke="#fff" stroke-width="1.8"><circle cx="12" cy="12" r="9"/><path d="M7.5 12.5l3 3 6-6.5"/></svg></span>
      <p class="body-text">Our reliable, friendly installation engineers work as part of a team that goes that extra mile to ensure projects are completed on time and to the highest standard.</p>
    </div>
    <div class="feature feature--3">
      <span class="feature-icon"><svg width="22" height="22" viewBox="0 0 24 24" fill="none" stroke="#fff" stroke-width="1.5"><circle cx="12" cy="12" r="3.2"/><path d="M12 2.5v3M12 18.5v3M2.5 12h3M18.5 12h3M5.3 5.3l2.1 2.1M16.6 16.6l2.1 2.1M5.3 18.7l2.1-2.1M16.6 7.4l2.1-2.1"/><circle cx="12" cy="12" r="6.5"/></svg></span>
      <p class="body-text">Using only recognised brands for our installations, our trained, accredited installers ensure clients get the highest quality install with the confidence that their system will last.</p>
    </div>

    <div class="abs cta">CONTACT US FOR MORE INFORMATION</div>
    <div class="abs footer-contacts">
      <span class="contact"><svg width="13" height="13" viewBox="0 0 24 24"><path fill="var(--orange)" d="M6.6 10.8a15.1 15.1 0 0 0 6.6 6.6l2.2-2.2a1 1 0 0 1 1-.25 11.4 11.4 0 0 0 3.6.57 1 1 0 0 1 1 1V20a1 1 0 0 1-1 1A17 17 0 0 1 3 4a1 1 0 0 1 1-1h3.5a1 1 0 0 1 1 1c0 1.25.2 2.45.57 3.57a1 1 0 0 1-.25 1z"/></svg>0800 555 0142</span>
      <span class="contact"><svg width="15" height="11" viewBox="0 0 18 14"><rect width="18" height="14" rx="1" fill="var(--orange)"/><path d="M1 1l8 6 8-6" fill="none" stroke="var(--black)" stroke-width="1.5"/></svg>info@harlowclimawell.co</span>
      <span class="contact"><svg width="13" height="13" viewBox="0 0 16 16"><g fill="none" stroke="var(--orange)" stroke-width="1.4"><circle cx="8" cy="8" r="7"/><ellipse cx="8" cy="8" rx="3" ry="7"/><path d="M1 8h14M2.5 4.5h11M2.5 11.5h11"/></g></svg>www.harlowclimawell.co</span>
    </div>
  </article>

</main>
</body>
</html>
```